Sophisticated, clean website reflecting my feminine, playful side to sell my abstract art,

I need a website no more than 3 pages to showcase my paintings, a little about me and some contact info. I do abstracts so looking for something a little edgy, yet feminine and current.
Updates

Hi there, These are some artists websites that I Iike: Marnelvoss.com (I like how airy it is) peterwallombry.com garethpolvens.com (I like how it scrolls) I'll need a place for a photo ( a headshot-i do not have it yet so I'll need to be able to upload that later) as well as an area for my bio. Also, it's important that I will be able to upload any new photos and descriptions easily so it should be user friendly. Lastly, I like in a sunny place so would like to have this seem upbeat and playful as that is how i like to paint. thanks-I'm trying to upload my photos now -

Target Market(s)

ppl ages 35-70 who want large scale art for their homes

Industry/Entity Type

art

Coding

Coded - Design and coding required

Number of Pages Required

3 page

Colors

Designer to choose colors to be used in the design.

Requirements
Must have
• photos of my art, a place for my bio, be easy to reach me. tasteful-nothing too "in your face" -my clients are pretty high end and organized. They like clean lines
Nice to have
• sophisticated background, muted tones in the back-similar clean font throughout-no cursive
Should not have
• too many dark areas. Too many blocks of color. Too serious.

```html
<!DOCTYPE html>
<html lang="en">
<head>
<meta charset="utf-8">
<title>Maren Castell – Home Page Variants</title>
<link href="https://fonts.googleapis.com/css2?family=Montserrat:wght@300;400;700&family=Quicksand:wght@400;500&display=swap" rel="stylesheet">
<style>
  :root{
    --board:#a9a9a9;
    --page-soft:#f5f5f5;
    --page-white:#ffffff;
    --ink:#1b1b1b;
    --ink-soft:#3a3a3a;
    --rule:#cfcfcf;
    --frame:#bdbdbd;
    --frame-dark:#555555;
    --button:#000000;
    --hero-a:#2f8a3c;
    --hero-b:#5cb85a;
    --hero-c:#1f6a6e;
    --hero-d:#d9c96a;
    --hero-e:#e6e2ea;
    --art-a:#5a3f82;
    --art-b:#8f6aa8;
    --art-c:#d9cbbd;
    --art-d:#2e3a6e;
  }
  *{box-sizing:border-box;margin:0;padding:0}
  html,body{width:1163px;height:1200px;overflow:hidden}
  body{background:var(--board);position:relative;font-family:"Quicksand",sans-serif;color:var(--ink)}

  .page{position:absolute;top:26px;width:800px;transform:scale(0.6122);transform-origin:0 0;background:var(--page-soft);overflow:hidden}
  .page--soft{left:81px;height:1890px}
  .page--white{left:618px;height:1844px;background:var(--page-white)}

  .site-header{position:absolute;left:0;top:0;width:800px;height:67px;background:var(--page-white);border-bottom:1px solid var(--rule);display:flex;align-items:center;justify-content:center;gap:12px}
  .brand-name{font-family:"Montserrat",sans-serif;font-weight:300;font-size:30px;letter-spacing:.5px;color:var(--ink)}
  .brand-mark{width:28px;height:28px;background:var(--ink)}

  .main-nav{position:absolute;left:0;top:67px;width:800px;height:41px;background:var(--page-white);font-size:11px;letter-spacing:.3px}
  .main-nav a{position:absolute;top:14px;color:var(--ink);text-decoration:none}
  .main-nav .is-active::after{content:"";position:absolute;left:0;right:0;top:17px;height:1px;background:var(--ink)}
  .handle{display:flex;align-items:center;gap:5px}
  .handle-dot{width:20px;height:20px;border-radius:50%;background:var(--ink)}
  .main-nav .handle{position:absolute;left:607px;top:10px;font-size:11px}

  .hero{position:absolute;left:0;top:108px;width:800px;height:432px;
    background:
      radial-gradient(ellipse at 85% 10%,var(--hero-d) 0,transparent 35%),
      radial-gradient(ellipse at 10% 70%,var(--hero-e) 0,transparent 30%),
      radial-gradient(ellipse at 55% 70%,var(--hero-c) 0,transparent 40%),
      linear-gradient(135deg,var(--hero-b),var(--hero-a) 55%,var(--hero-c))}
  .slider-label{position:absolute;left:64px;top:500px;font-family:"Montserrat",sans-serif;font-weight:700;font-size:12px;color:#fff;letter-spacing:.5px}
  .slider-btn{position:absolute;top:527px;width:44px;height:28px;background:var(--button)}
  .slider-btn svg{display:block;margin:7px auto 0}

  .about-photo{position:absolute;left:52px;top:610px;width:262px;height:291px;border:1px solid var(--frame);background:var(--page-white);padding:8px}
  .about-photo--dark{border-color:var(--frame-dark)}
  .about-photo div{width:100%;height:100%;background:linear-gradient(180deg,#dcdcdc 0,#d6d6d6 30%,#8fb0cf 60%,#7da2c6 100%)}
  .section-title{font-family:"Montserrat",sans-serif;font-weight:300;color:var(--ink);position:absolute}
  .title-rule{position:absolute;height:2px;width:44px;background:var(--ink-soft)}
  .about-title{left:362px;top:630px;font-size:32px}
  .about-text{position:absolute;left:362px;top:697px;width:410px;font-size:12.6px;line-height:18px;color:var(--ink-soft)}
  .about-text p{margin-bottom:10px}

  .gallery-title{left:0;width:820px;text-align:center;top:1006px;font-size:26px}
  .gallery-frame{position:absolute;left:155px;top:1068px;width:505px;height:306px;border:5px solid var(--frame);background:var(--page-white);padding:4px}
  .gallery-frame div{width:100%;height:100%;background:
      radial-gradient(circle at 20% 30%,var(--art-d) 0,transparent 25%),
      radial-gradient(circle at 80% 35%,var(--art-c) 0,transparent 30%),
      radial-gradient(circle at 40% 75%,var(--art-b) 0,transparent 35%),
      linear-gradient(120deg,var(--art-a),var(--art-b) 50%,var(--art-a))}
  .gallery-arrow{position:absolute;top:1199px}

  .contact-title{left:0;width:800px;text-align:center;top:1466px;font-size:32px}
  .contact-lead{position:absolute;left:0;width:800px;text-align:center;top:1525px;font-size:13px}
  .contact-item{position:absolute;top:1583px;display:flex;align-items:center;gap:12px}
  .contact-icon{width:44px;height:44px;border:1px solid var(--ink-soft);display:flex;align-items:center;justify-content:center}
  .contact-label{font-size:12px;line-height:18px}
  .contact-value{font-size:14px;line-height:20px}
  .contact-value--sm{font-size:13px}

  .site-footer{position:absolute;left:0;top:1748px;width:800px;border-top:1px solid var(--rule);font-size:11px;text-align:center}
  .footer-nav{position:absolute;left:0;width:800px;top:28px;display:flex;justify-content:center;gap:44px;font-size:11.5px}
  .footer-copy{position:absolute;left:0;width:800px;font-size:10px}
  .site-footer .handle{position:absolute;left:0;width:800px;justify-content:center;font-size:11px}
</style>
</head>
<body>

<!-- Variant A: soft grey page with full footer navigation -->
<section class="page page--soft">
  <header class="site-header"><span class="brand-mark"></span><span class="brand-name">MAREN CASTELL</span></header>
  <nav class="main-nav">
    <a class="is-active" style="left:123px">HOME</a>
    <a style="left:229px">ABOUT ME</a>
    <a style="left:361px">GALLERY</a>
    <a style="left:485px">CONTACT</a>
    <span class="handle"><span class="handle-dot"></span>@mcastellart</span>
  </nav>
  <div class="hero" role="img" aria-label="Abstract green and teal painting slideshow"></div>
  <span class="slider-label">PLAY ▸</span>
  <span class="slider-btn" style="left:60px"><svg width="12" height="14"><path d="M10 1 L2 7 L10 13Z" fill="#fff"/></svg></span>
  <span class="slider-btn" style="left:111px"><svg width="12" height="14"><path d="M2 1 L10 7 L2 13Z" fill="#fff"/></svg></span>

  <figure class="about-photo"><div role="img" aria-label="Portrait of the artist"></div></figure>
  <h2 class="section-title about-title">ABOUT ME</h2>
  <span class="title-rule" style="left:364px;top:673px"></span>
  <div class="about-text">
    <p>Lorem ipsum dolor sit amet, consectetur adipiscing elit, sed do eiusmod tempor incididunt ut labore et dolore magna aliqua. Ut enim ad minim veniam, quis nostrud exercitation</p>
    <p>Duis aute irure dolor in reprehenderit in voluptate velit esse cillum<br>dolore eu fugiat nulla pariatur. Excepteur sint occaecat cupidatat non proident, sunt in culpa qui officia deserunt mollit anim id est laborum</p>
    <p>Sed ut perspiciatis unde pariatur. Excepteur sint occaecat cupidatat non proident, sunt in culpa qui officia deserunt mollit anim id est laborum.Sed ut persmollit anim id est laborum.</p>
  </div>

  <h2 class="section-title gallery-title">PHOTO GALLERY</h2>
  <span class="title-rule" style="left:390px;top:1041px;width:42px"></span>
  <div class="gallery-frame"><div role="img" aria-label="Abstract purple floral painting"></div></div>
  <svg class="gallery-arrow" style="left:104px" width="24" height="46"><path d="M22 1 L2 23 L22 45" fill="none" stroke="#333" stroke-width="2"/></svg>
  <svg class="gallery-arrow" style="left:683px" width="24" height="46"><path d="M2 1 L22 23 L2 45" fill="none" stroke="#333" stroke-width="2"/></svg>

  <h2 class="section-title contact-title">CONTACT US</h2>
  <span class="title-rule" style="left:370px;top:1509px;width:60px"></span>
  <p class="contact-lead">Please get in touch with me on below details.</p>
  <div class="contact-item" style="left:89px">
    <span class="contact-icon"><svg width="22" height="16"><rect x="1" y="1" width="20" height="14" fill="none" stroke="#333"/><path d="M1 1 L11 9 L21 1 M1 15 L8 7 M21 15 L14 7" fill="none" stroke="#333"/></svg></span>
    <span><span class="contact-label">Email address</span><br><span class="contact-value">marencastell@info.com</span></span>
  </div>
  <div class="contact-item" style="left:337px">
    <span class="contact-icon"><svg width="20" height="20"><path d="M4 1 L8 5 L6 8 Q9 13 12 14 L15 12 L19 16 L16 19 Q6 18 1 4Z" fill="none" stroke="#333"/></svg></span>
    <span><span class="contact-label">Phone number</span><br><span class="contact-value">(123) 456 7890</span></span>
  </div>
  <div class="contact-item" style="left:540px">
    <span class="contact-icon"></span>
    <span><span class="contact-label">Follow my studio feed</span><br><span class="contact-value contact-value--sm">@mcastellart</span></span>
  </div>

  <footer class="site-footer">
    <div class="footer-nav"><span>HOME</span><span>ABOUT ME</span><span>GALLERY</span><span>CONTACT</span></div>
    <p class="footer-copy" style="top:58px">© 2022 Maren Castell &nbsp;All Rights Reserved</p>
    <span class="handle" style="top:83px"><span class="handle-dot"></span>@mcastellart</span>
  </footer>
</section>

<!-- Variant B: white page with compact footer -->
<section class="page page--white">
  <header class="site-header"><span class="brand-name">MAREN CASTELL</span></header>
  <nav class="main-nav">
    <a class="is-active" style="left:123px">HOME</a>
    <a style="left:229px">ABOUT ME</a>
    <a style="left:361px">GALLERY</a>
    <a style="left:485px">CONTACT</a>
    <span class="handle"><span class="handle-dot"></span>@mcastellart</span>
  </nav>
  <div class="hero" role="img" aria-label="Abstract green and teal painting slideshow"></div>
  <span class="slider-label">PLAY ▸</span>
  <span class="slider-btn" style="left:60px"><svg width="12" height="14"><path d="M10 1 L2 7 L10 13Z" fill="#fff"/></svg></span>
  <span class="slider-btn" style="left:111px"><svg width="12" height="14"><path d="M2 1 L10 7 L2 13Z" fill="#fff"/></svg></span>

  <figure class="about-photo about-photo--dark"><div role="img" aria-label="Portrait of the artist"></div></figure>
  <h2 class="section-title about-title">ABOUT ME</h2>
  <span class="title-rule" style="left:364px;top:673px"></span>
  <div class="about-text">
    <p>Lorem ipsum dolor sit amet, consectetur adipiscing elit, sed do eiusmod tempor incididunt ut labore et dolore magna aliqua. Ut enim ad minim veniam, quis nostrud exercitation</p>
    <p>Duis aute irure dolor in reprehenderit in voluptate velit esse cillum<br>dolore eu fugiat nulla pariatur. Excepteur sint occaecat cupidatat non proident, sunt in culpa qui officia deserunt mollit anim id est laborum</p>
    <p>Sed ut perspiciatis unde pariatur. Excepteur sint occaecat cupidatat non proident, sunt in culpa qui officia deserunt mollit anim id est laborum.Sed ut persmollit anim id est laborum.</p>
  </div>

  <h2 class="section-title gallery-title">PHOTO GALLERY</h2>
  <span class="title-rule" style="left:390px;top:1041px;width:42px"></span>
  <div class="gallery-frame"><div role="img" aria-label="Abstract purple floral painting"></div></div>
  <svg class="gallery-arrow" style="left:104px" width="24" height="46"><path d="M22 1 L2 23 L22 45" fill="none" stroke="#333" stroke-width="2"/></svg>
  <svg class="gallery-arrow" style="left:683px" width="24" height="46"><path d="M2 1 L22 23 L2 45" fill="none" stroke="#333" stroke-width="2"/></svg>

  <h2 class="section-title contact-title">CONTACT US</h2>
  <span class="title-rule" style="left:370px;top:1509px;width:60px"></span>
  <p class="contact-lead">Please get in touch with me on below details.</p>
  <div class="contact-item" style="left:89px">
    <span class="contact-icon"><svg width="22" height="16"><rect x="1" y="1" width="20" height="14" fill="none" stroke="#333"/><path d="M1 1 L11 9 L21 1 M1 15 L8 7 M21 15 L14 7" fill="none" stroke="#333"/></svg></span>
    <span><span class="contact-label">Email address</span><br><span class="contact-value">marencastell@info.com</span></span>
  </div>
  <div class="contact-item" style="left:337px">
    <span class="contact-icon"><svg width="20" height="20"><path d="M4 1 L8 5 L6 8 Q9 13 12 14 L15 12 L19 16 L16 19 Q6 18 1 4Z" fill="none" stroke="#333"/></svg></span>
    <span><span class="contact-label">Phone number</span><br><span class="contact-value">(123) 456 7890</span></span>
  </div>
  <div class="contact-item" style="left:540px">
    <span class="contact-icon"></span>
    <span><span class="contact-label">Follow my studio feed</span><br><span class="contact-value contact-value--sm">@mcastellart</span></span>
  </div>

  <footer class="site-footer">
    <p class="footer-copy" style="top:18px">© 2022 Maren Castell &nbsp;All Rights Reserved</p>
    <span class="handle" style="top:42px"><span class="handle-dot"></span>@mcastellart</span>
  </footer>
</section>

</body>
</html>
```